Moravel Aesthetic Doctor

I require an elegant, luxurious looking business card for my aesthetic business. I am a doctor and that will set me aside from competitors. I am planning to provide home and spa based treatments to clients with high expectations. I have attached my logo.

```html
<!DOCTYPE html>
<html lang="en">
<head>
<meta charset="utf-8">
<title>Moravel Aesthetic Doctor – Business Card</title>
<link rel="stylesheet" href="https://fonts.googleapis.com/css2?family=Roboto:wght@300;400;500&display=swap">
<style>
  :root {
    --page-bg: #d9d9d9;
    --card-white: #ffffff;
    --sky: #6cc3ea;
    --sky-soft: #a9dcf2;
    --grey-text: #9a9c9f;
    --grey-band: #a7a9ac;
    --back-top: #aee0f4;
    --back-mid: #a9abae;
    --white: #ffffff;
  }
  * { box-sizing: border-box; margin: 0; padding: 0; }
  html, body {
    width: 1125px; height: 1200px; overflow: hidden;
    background: var(--page-bg);
    font-family: "Roboto", sans-serif;
  }
  .card {
    position: absolute; left: 150px; width: 826px; height: 472px;
    border-radius: 22px; overflow: hidden;
  }
  .card-front { top: 98px; background: var(--card-white); }
  .card-back {
    top: 632px;
    background: linear-gradient(180deg, var(--back-top) 0%, #b7c3ca 18%, var(--back-mid) 50%, #b3c2ca 82%, var(--back-top) 100%);
  }

  /* front */
  .front-wordmark { position: absolute; left: 50px; top: 40px; color: var(--grey-text); font-weight: 300; line-height: 1; }
  .front-wordmark .name { font-size: 58px; letter-spacing: 2px; }
  .front-wordmark .tag { font-size: 24px; letter-spacing: 2px; margin-top: 6px; }
  .front-decor {
    position: absolute; left: 380px; top: 20px; width: 430px; height: 390px; border-radius: 50%;
    background: radial-gradient(circle at 50% 50%, rgba(200,225,240,0.45), rgba(235,242,248,0.2) 65%, rgba(255,255,255,0) 72%);
  }
  .doctor { position: absolute; left: 50px; top: 237px; }
  .doctor-name { color: var(--sky); font-size: 31px; font-weight: 500; }
  .doctor-name .post { font-size: 19px; font-weight: 500; margin-left: 4px; }
  .doctor-cred { color: var(--grey-text); font-size: 21px; font-weight: 400; margin-top: 8px; }
  .contact { position: absolute; left: 50px; top: 322px; color: var(--grey-text); font-size: 22px; font-weight: 400; }
  .contact-row { display: flex; align-items: center; gap: 12px; height: 33px; }
  .contact-row svg { width: 20px; height: 20px; }
  .social { display: flex; gap: 18px; margin-left: 30px; }
  .social span { width: 26px; height: 26px; border-radius: 50%; background: var(--sky-soft); }
  .front-band { position: absolute; left: 0; bottom: 0; width: 826px; height: 80px; }
  .website { position: absolute; right: 40px; bottom: 16px; color: var(--white); font-size: 21px; font-weight: 400; }

  /* back */
  .back-decor {
    position: absolute; left: 300px; top: 20px; width: 440px; height: 420px; border-radius: 50%;
    background: radial-gradient(circle, rgba(255,255,255,0.14), rgba(255,255,255,0.04) 65%, rgba(255,255,255,0) 72%);
  }
  .back-logo { position: absolute; left: 150px; top: 130px; display: flex; align-items: center; gap: 28px; }
  .back-logo .mark-circle { width: 150px; height: 150px; border-radius: 50%; border: 4px solid var(--white); }
  .back-wordmark { color: var(--white); font-weight: 300; line-height: 1; }
  .back-wordmark .name { font-size: 76px; letter-spacing: 3px; }
  .back-wordmark .tag { font-size: 32px; letter-spacing: 3px; margin-top: 10px; }
  .services { position: absolute; left: 0; right: 0; top: 318px; text-align: center; color: var(--white); font-size: 22px; font-weight: 300; line-height: 33px; }
  .services .dot { display: inline-block; width: 8px; height: 8px; border-radius: 50%; background: var(--white); margin: 0 6px 3px; }
</style>
</head>
<body>
  <section class="card card-front">
    <div class="front-decor" role="img" aria-label="Faint brand artwork background area"></div>
    <div class="front-wordmark">
      <div class="name">MORAVEL</div>
      <div class="tag">AESTHETIC DOCTOR</div>
    </div>
    <div class="doctor">
      <div class="doctor-name">Dr Elsa Varden,<span class="post">MRCPCH MD</span></div>
      <div class="doctor-cred">Australasian Diploma of Aesthetic Medicine</div>
    </div>
    <div class="contact">
      <div class="contact-row">
        <svg viewBox="0 0 24 24" aria-hidden="true"><path fill="#6cc3ea" d="M6.6 10.8a15 15 0 0 0 6.6 6.6l2.2-2.2c.3-.3.7-.4 1-.2 1.1.4 2.3.6 3.6.6.6 0 1 .4 1 1V20c0 .6-.4 1-1 1A17 17 0 0 1 3 4c0-.6.4-1 1-1h3.5c.6 0 1 .4 1 1 0 1.3.2 2.5.6 3.6.1.3 0 .7-.2 1z"/></svg>
        <span>0800 555 018</span>
      </div>
      <div class="contact-row">
        <svg viewBox="0 0 24 24" aria-hidden="true"><rect x="3" y="6" width="18" height="12" rx="1.5" fill="none" stroke="#6cc3ea" stroke-width="1.8"/><path d="M3.5 7l8.5 6 8.5-6" fill="none" stroke="#6cc3ea" stroke-width="1.8"/></svg>
        <span>elsa@moravel.co.nz</span>
        <div class="social" aria-hidden="true"><span></span><span></span></div>
      </div>
    </div>
    <svg class="front-band" viewBox="0 0 826 80" preserveAspectRatio="none" aria-hidden="true">
      <path d="M120 80 Q400 8 826 6 L826 80 Z" fill="#a7a9ac"/>
      <path d="M0 78 Q300 6 700 0 Q330 18 40 80 Z" fill="#6cc3ea"/>
    </svg>
    <div class="website">www.moravel.co.nz</div>
  </section>

  <section class="card card-back">
    <div class="back-decor" role="img" aria-label="Faint brand artwork background area"></div>
    <div class="back-logo">
      <div class="mark-circle" aria-hidden="true"></div>
      <div class="back-wordmark">
        <div class="name">MORAVEL</div>
        <div class="tag">AESTHETIC DOCTOR</div>
      </div>
    </div>
    <div class="services">
      <div>Dermal injectables<span class="dot"></span>Plasma facials<span class="dot"></span>Microneedling</div>
      <div>Skin boosters<span class="dot"></span>Excessive sweating</div>
      <div>Home and Spa Based Treatments</div>
    </div>
  </section>
</body>
</html>
```